Design for Viral Content Website

In need of a webdesign for a website with mostly Buzz Tales. There are three versions of a landingpage:
a) Whole article on one page
b) Article split into several pages each with image and previous/next buttons
c) Mobile version
I uploaded very rough versions of how it should look like. Don't judge me, if I would be a designer, I'd do it myself ;)
Don't have a mockup for the index/category listing, surprise me :)
The header must be small (as here on framebazaar) because it will be fixed and scroll when the user scrolls down.
4 page

```html
<!DOCTYPE html>
<html lang="en">
<head>
<meta charset="utf-8">
<title>Buzz Tales – Article</title>
<link href="https://fonts.googleapis.com/css2?family=Raleway:wght@400;500;600;700&family=Kalam&display=swap" rel="stylesheet">
<style>
:root{
  --brand:#3f5aa9;
  --brand-dark:#33498f;
  --nav:#2a2a2a;
  --page:#f1f1f1;
  --card:#ffffff;
  --ink:#1d1d1d;
  --muted:#a9a9a9;
  --share-fb:#3b5998;
  --share-tw:#55acee;
  --share-gp:#dd4b39;
  --share-rd:#ff5a1f;
  --share-pi:#cb2027;
  --share-li:#0e76a8;
  --share-su:#4caf50;
  --yt:#e52d27;
}
*{box-sizing:border-box;margin:0;padding:0}
html,body{width:891px;height:1200px;overflow:hidden}
body{font-family:"Raleway",sans-serif;color:var(--ink);background:var(--page)}
.page{position:relative;width:891px;height:1200px;background:var(--page)}

/* header */
.site-header{position:absolute;left:0;top:0;width:891px;height:64px;background:var(--card)}
.brand-name{position:absolute;left:56px;top:13px;font-size:31px;font-weight:700;color:var(--brand);letter-spacing:-.5px}
.social{position:absolute;left:644px;top:22px;display:flex;gap:4px;align-items:center}
.social .sq{width:25px;height:25px;border-radius:4px}
.like{margin-left:2px;height:25px;padding:0 8px;background:var(--share-fb);color:#fff;font-size:13px;font-weight:600;line-height:25px;border-radius:2px}
.like-count{height:25px;padding:0 5px;border:1px solid #888;border-radius:3px;font-size:13px;line-height:23px;color:#333;background:#fff}

.main-nav{position:absolute;left:0;top:64px;width:891px;height:38px;background:var(--nav);display:flex;justify-content:center;align-items:center;gap:24px}
.main-nav a{color:#eee;text-decoration:none;font-size:12px;font-weight:500;letter-spacing:.2px}
.main-nav svg{vertical-align:middle;margin-left:2px}

/* top strip */
.strip-item{position:absolute;top:110px;width:122px}
.strip-item .ph{width:122px;height:69px}
.strip-item p{margin-top:5px;font-size:11.5px;font-weight:500;color:#333;padding-left:2px;letter-spacing:.3px}

/* cards */
.card{position:absolute;background:var(--card)}
.article-title{left:56px;top:213px;width:516px;height:139px;display:flex;align-items:center;justify-content:center;text-align:center;font-size:28px;font-weight:500;line-height:1.18;padding:0 6px;letter-spacing:-.2px}
.pager{position:absolute;left:56px;top:364px;width:516px;height:20px;font-size:13px;font-weight:500}
.pager .prev{position:absolute;left:0;top:0;display:flex;align-items:center;gap:5px;color:var(--brand)}
.pager .next{position:absolute;right:0;top:0;display:flex;align-items:center;gap:5px;color:var(--brand)}
.pager .box{width:21px;height:21px;border:1.5px solid var(--brand);border-radius:3px;display:flex;align-items:center;justify-content:center}
.pager .count{position:absolute;left:240px;top:2px;color:#222}

.image-card{left:56px;top:395px;width:516px;height:367px}
.image-card h2{position:absolute;left:9px;top:8px;font-size:17px;font-weight:400;color:var(--brand)}
.image-card .lede{position:absolute;left:9px;top:36px;width:490px;font-size:9.5px;line-height:1.15;color:#222}
.image-card .ph{position:absolute;left:9px;top:67px;width:497px;height:270px}
.image-card .via{position:absolute;left:0;width:516px;top:347px;text-align:center;font-size:10px;color:#333}
.image-card .via span{color:var(--brand)}

.share-row{position:absolute;left:56px;top:774px;height:30px;display:flex;gap:7px;align-items:center}
.share-main{width:132px;height:30px;background:var(--share-fb);color:#fff;font-size:9.5px;font-weight:700;letter-spacing:.8px;display:flex;align-items:center;justify-content:center;border-radius:2px}
.share-btn{width:30px;height:30px;border-radius:2px}
.caring{position:absolute;left:442px;top:776px;font-family:"Kalam",cursive;font-size:13px;color:var(--brand);transform:rotate(-4deg)}

.grid-card{left:56px;top:813px;width:516px;height:331px}
.tile{position:absolute;width:159px}
.tile .ph{width:159px;height:118px}
.tile p{margin-top:6px;font-size:12.5px;font-weight:500;color:#222;padding-left:1px}

.show-more{position:absolute;left:265px;top:1161px;width:100px;text-align:center;font-size:12px;color:var(--brand)}

/* sidebar */
.sidebar{left:582px;top:213px;width:252px;height:801px}
.sidebar-head{position:absolute;left:8px;top:9px;width:236px;height:30px;background:var(--brand);color:#fff;font-size:11.5px;font-weight:500;line-height:30px;padding-left:8px}
.rec{position:absolute;left:8px;width:236px}
.rec .ph{width:236px;height:126px}
.rec h3{margin-top:7px;font-size:12.5px;font-weight:500;color:#111}
.meta{margin-top:7px;display:flex;justify-content:space-between;font-size:7px;color:var(--muted)}
.meta span{display:flex;align-items:center;gap:2px}
.meta i{display:inline-block;width:6px;height:6px;background:#ccc;border-radius:1px}

.newsletter{left:582px;top:1026px;width:252px;height:118px;background:var(--brand);color:#fff;text-align:center}
.newsletter h4{margin-top:16px;font-size:12.5px;font-weight:500}
.newsletter p{margin-top:6px;font-size:8.5px;line-height:1.3}
.newsletter .field{position:absolute;left:10px;top:79px;width:165px;height:22px;border-bottom:1px solid #8193c9;text-align:left;font-size:9px;color:#8e9fd2;line-height:22px}
.newsletter .submit{position:absolute;left:182px;top:79px;width:62px;height:21px;background:#fff;color:var(--brand);font-size:10px;line-height:21px}

.site-footer{position:absolute;left:600px;top:1162px;width:232px;text-align:center;font-size:8.5px;color:#222}
.site-footer nav{display:flex;justify-content:center;gap:7px}
.site-footer p{margin-top:3px}
</style>
</head>
<body>
<div class="page">

  <header class="site-header">
    <div class="brand-name">Buzz Tales</div>
    <div class="social">
      <span class="sq" style="background:var(--share-fb)"></span>
      <span class="sq" style="background:var(--share-tw)"></span>
      <span class="sq" style="background:var(--yt)"></span>
      <span class="like">Like</span>
      <span class="like-count">60k</span>
    </div>
  </header>

  <nav class="main-nav">
    <a>HOMEPAGE</a><a>VIRAL</a><a>PAGELINK</a>
    <a>PAGELINK<svg width="7" height="5" viewBox="0 0 7 5"><path d="M1 1l2.5 2.5L6 1" stroke="#eee" fill="none"/></svg></a>
    <a>PAGELINK</a><a>ABOUT US</a><a>PRIVACY POLICY</a><a>CONTACT US</a>
  </nav>

  <div class="strip-item" style="left:58px"><div class="ph" role="img" aria-label="Photo of people at an awards show" style="background:linear-gradient(135deg,#3a3230,#141414)"></div><p>Article title here</p></div>
  <div class="strip-item" style="left:188px"><div class="ph" role="img" aria-label="Photo of a grumpy-looking cat" style="background:linear-gradient(135deg,#4d8bd0,#b8a48e)"></div><p>Article title here</p></div>
  <div class="strip-item" style="left:319px"><div class="ph" role="img" aria-label="Photo of cheerleaders on a field" style="background:linear-gradient(135deg,#c9d4e6,#6f8f3e)"></div><p>Article title here</p></div>
  <div class="strip-item" style="left:449px"><div class="ph" role="img" aria-label="Photo of two babies in knitted hats" style="background:linear-gradient(135deg,#7a8b8a,#c79a82)"></div><p>Article title here</p></div>
  <div class="strip-item" style="left:579px"><div class="ph" role="img" aria-label="Photo of a wedding couple" style="background:linear-gradient(135deg,#e8e6e4,#4e4a4d)"></div><p>Article title here</p></div>
  <div class="strip-item" style="left:709px"><div class="ph" role="img" aria-label="Before and after fitness photo" style="background:linear-gradient(135deg,#b79a86,#6f5d52)"></div><p>Article title here</p></div>

  <section class="card article-title">Title of this article will be goes here,<br>how many line you want no issue<br>the numbers of lines.</section>

  <div class="pager">
    <span class="prev"><span class="box"><svg width="8" height="10" viewBox="0 0 8 10"><path d="M6 1L2 5l4 4" stroke="#3f5aa9" stroke-width="1.5" fill="none"/></svg></span>Previous</span>
    <span class="count">5 / 50</span>
    <span class="next">Next<span class="box"><svg width="8" height="10" viewBox="0 0 8 10"><path d="M2 1l4 4-4 4" stroke="#3f5aa9" stroke-width="1.5" fill="none"/></svg></span></span>
  </div>

  <article class="card image-card">
    <h2>Image #1 Title will be here</h2>
    <p class="lede">Lorem Ipsum is simply dummy text of the printing and typesetting industry. Lorem Ipsum has been the industry's standard dummy text ever since the 1500s</p>
    <div class="ph" role="img" aria-label="Photo of friends celebrating at a college party" style="background:linear-gradient(135deg,#8a6a4c,#2c2420 55%,#b08a6a)"></div>
    <p class="via">via <span>picshare</span></p>
  </article>

  <div class="share-row">
    <span class="share-main">SHARE</span>
    <span class="share-btn" style="background:var(--share-tw)"></span>
    <span class="share-btn" style="background:var(--share-gp)"></span>
    <span class="share-btn" style="background:var(--share-rd)"></span>
    <span class="share-btn" style="background:var(--share-pi)"></span>
    <span class="share-btn" style="background:var(--share-li)"></span>
    <span class="share-btn" style="background:var(--share-su)"></span>
  </div>
  <span class="caring">Sharing is caring!</span>

  <section class="card grid-card">
    <div class="tile" style="left:10px;top:13px"><div class="ph" role="img" aria-label="Photo of a cat wearing a costume mask" style="background:linear-gradient(135deg,#d8d4cf,#5e5853)"></div><p>Article title will be here.</p></div>
    <div class="tile" style="left:178px;top:13px"><div class="ph" role="img" aria-label="Photo of a newborn's feet held in hands" style="background:linear-gradient(135deg,#a78b7b,#d7b3a4)"></div><p>Article title will be here.</p></div>
    <div class="tile" style="left:347px;top:13px"><div class="ph" role="img" aria-label="Photo of an ice-covered lighthouse" style="background:linear-gradient(180deg,#6f8aa8,#dfe6ec)"></div><p>Article title will be here.</p></div>
    <div class="tile" style="left:10px;top:176px"><div class="ph" role="img" aria-label="Photo of a celebrity group selfie" style="background:linear-gradient(135deg,#6a3a33,#1c1a1a)"></div><p>Article title will be here.</p></div>
    <div class="tile" style="left:178px;top:176px"><div class="ph" role="img" aria-label="Photo of an ice bucket challenge" style="background:linear-gradient(135deg,#a5533e,#3e6a56)"></div><p>Article title will be here.</p></div>
    <div class="tile" style="left:347px;top:176px"><div class="ph" role="img" aria-label="Photo of a performer on stage" style="background:linear-gradient(135deg,#c7c8cc,#3a3f4a)"></div><p>Article title will be here.</p></div>
  </section>

  <div class="show-more">Show More<br><svg width="9" height="6" viewBox="0 0 9 6"><path d="M1 1l3.5 3.5L8 1" stroke="#3f5aa9" fill="none"/></svg></div>

  <aside class="card sidebar">
    <div class="sidebar-head">Recommended for you:</div>
    <div class="rec" style="top:47px"><div class="ph" role="img" aria-label="Photo of a baby with a large snake" style="background:linear-gradient(135deg,#5a5044,#c89a8c)"></div><h3>Article title will be here in lines.</h3><div class="meta"><span><i></i>Admin Name</span><span><i></i>1 day ago</span><span><i></i>99 comments</span></div></div>
    <div class="rec" style="top:240px"><div class="ph" role="img" aria-label="Photo of a giant ball crushing a car" style="background:linear-gradient(135deg,#8a8a8a,#2b2b2b)"></div><h3>Article title will be here in lines.</h3><div class="meta"><span><i></i>Admin Name</span><span><i></i>1 day ago</span><span><i></i>99 comments</span></div></div>
    <div class="rec" style="top:430px"><div class="ph" role="img" aria-label="Photo of a makeup tutorial" style="background:linear-gradient(135deg,#5a3f52,#d9b7a8)"></div><h3>Article title will be here in lines.</h3><div class="meta"><span><i></i>Admin Name</span><span><i></i>1 day ago</span><span><i></i>99 comments</span></div></div>
    <div class="rec" style="top:619px"><div class="ph" role="img" aria-label="Black and white historical portraits" style="background:linear-gradient(135deg,#d0d0d0,#4a4a4a)"></div><h3>Article title will be here in lines.</h3><div class="meta"><span><i></i>Admin Name</span><span><i></i>1 day ago</span><span><i></i>99 comments</span></div></div>
  </aside>

  <section class="card newsletter">
    <h4>GET MORE VIRAL IN YOUR INBOX!</h4>
    <p>Sign up for our daily email newsletter for free<br>and get updated</p>
    <div class="field">Your email here</div>
    <div class="submit">Submit</div>
  </section>

  <footer class="site-footer">
    <nav><span>About</span><span>RSS</span><span>Privacy</span><span>Contact</span><span>Copyright</span></nav>
    <p>© 2016. All rights reserved.</p>
  </footer>

</div>
</body>
</html>
```